V.Lumo Gin - Bottle label Design

We are manufacturers of Gin in South Africa.
The name of our Gin is V.Lumo Gin with Q standing for Dlovikazi, a Xhosa Village in the region of Eastern Cape.

We would like our brand to depict the following (really the focus of Gold on it)
> Prosperity of the place
> Wealth of the place, land, material or in the people
> Gold rush, potential, hope

As the brand matures, we would like to have campaigns with it. See ideas below:
> V.Lumo Premium
> Crimson dusk edition
Limited edition will be released every year
- V.Lumo entabeni (location)
- V.Lumo ekhayeni (location)

> Each batch of bottles with focus on a specific area/location in Dlovikazi. One that is known and will be highlighted on the map design of the bottle.
Bottles based on landmarks in Dlovikazi and landmark design in the Big V.

Below we tried but we are not where we really want to be in terms of Gin Bottle elegance.

Target Market(s)

Target market is the young crowd. Young Xhosa men and women working really hard to get their goals. Positive thinkers. Elegant. Fresh. Bold. Age from 24 to 45. People who enjoy quality products.

Industry/Entity Type

Beverage Industry. Craft Gin.

Font styles to use
Sans Serif
Decorative

Colors
FFF300
FFF600
FEFA6F
FFFEC7
FFFEE8
FFC000
F8CF3A
FAE287
FDF2CF
FEFAEE

Requirements
Must have
• Gold colour as a theme. Try and make the background textured.

```html
<!DOCTYPE html>
<html lang="en">
<head>
<meta charset="utf-8">
<title>V.Lumo Gin – Bottle Label</title>
<link href="https://fonts.googleapis.com/css2?family=Montserrat:wght@800&family=Roboto:wght@400;500&family=Roboto+Condensed:wght@400;500&display=swap" rel="stylesheet">
<style>
  :root {
    --page: #ffffff;
    --label-black: #0b0b0a;
    --stripe: #171716;
    --gold-deep: #9c7a14;
    --gold: #d9b23a;
    --gold-bright: #f8cf3a;
    --gold-pale: #fae287;
    --ink-dark: #2a2108;
    --white: #f4f4f2;
  }
  * { box-sizing: border-box; margin: 0; padding: 0; }
  html, body { width: 1200px; height: 1200px; overflow: hidden; background: var(--page); }
  .canvas { position: relative; width: 1200px; height: 1200px; }

  .label {
    position: absolute; left: 100px; top: 108px; width: 1000px; height: 984px;
    background:
      repeating-linear-gradient(180deg, var(--label-black) 0 6px, var(--stripe) 6px 8px);
    border: 6px solid var(--gold-deep);
    overflow: hidden;
  }
  .label__frame {
    position: absolute; inset: 10px;
    border: 3px solid var(--gold);
    pointer-events: none;
  }
  .label__base-band {
    position: absolute; left: 0; right: 0; bottom: 16px; height: 22px;
    background: linear-gradient(90deg, var(--gold-deep), var(--gold-pale) 45%, var(--gold-bright) 60%, var(--gold-deep));
  }

  .landscape {
    position: absolute; left: 30px; right: 30px; top: 32px; height: 440px;
    background:
      radial-gradient(ellipse 55% 40% at 55% 30%, rgba(248,207,58,0.55), transparent 70%),
      linear-gradient(180deg, transparent 0%, rgba(156,122,20,0.35) 35%, rgba(217,178,58,0.45) 70%, rgba(11,11,10,0) 100%);
  }

  .brand {
    position: absolute; left: 0; right: 0; top: 392px;
    display: flex; align-items: center; justify-content: center; gap: 26px;
  }
  .brand__mark {
    width: 96px; height: 96px; border-radius: 50%;
    background: var(--gold-bright);
  }
  .brand__name {
    font-family: "Montserrat", sans-serif; font-weight: 800;
    font-size: 150px; line-height: 1; letter-spacing: -2px;
    color: var(--white);
  }

  .product-type {
    position: absolute; left: 0; right: 0; top: 660px;
    text-align: center;
    font-family: "Roboto", sans-serif; font-weight: 400;
    font-size: 104px; line-height: 1; letter-spacing: 4px;
    color: var(--white);
  }

  .details {
    position: absolute; left: 160px; top: 800px; width: 672px; height: 138px;
    background: linear-gradient(90deg, var(--gold-deep), var(--gold-pale) 40%, var(--gold) 70%, var(--gold-deep));
    padding: 6px;
  }
  .details__grid {
    width: 100%; height: 100%;
    border: 2px solid var(--ink-dark);
    display: grid; grid-template-columns: 1fr 168px; grid-template-rows: 1fr 1fr;
    font-family: "Roboto Condensed", sans-serif; color: var(--ink-dark);
  }
  .details__cell {
    display: flex; align-items: center; justify-content: center; text-align: center;
    border-bottom: 2px solid var(--ink-dark);
  }
  .details__cell--right { border-left: 2px solid var(--ink-dark); }
  .details__cell--last { border-bottom: none; }
  .details__story { font-size: 21px; line-height: 1.05; text-transform: uppercase; }
  .details__origin { font-size: 29px; font-weight: 500; letter-spacing: 3px; text-transform: uppercase; }
  .details__abv, .details__volume { font-size: 28px; font-weight: 500; }
</style>
</head>
<body>
  <main class="canvas">
    <section class="label">
      <div class="label__frame"></div>

      <div class="landscape" role="img" aria-label="Gold-foil engraving of the Dlovikazi village landscape: a hill with a tree on its crest above scattered homesteads"></div>

      <div class="brand">
        <span class="brand__mark"></span>
        <span class="brand__name">V.Lumo</span>
      </div>

      <p class="product-type">GIN</p>

      <div class="details">
        <div class="details__grid">
          <div class="details__cell">
            <p class="details__story">Triple distilled with the rich &amp;<br>aromatic taste of the Dlovikazi region</p>
          </div>
          <div class="details__cell details__cell--right">
            <p class="details__abv">40% alc.vol.</p>
          </div>
          <div class="details__cell details__cell--last">
            <p class="details__origin">Made in Eastern Cape</p>
          </div>
          <div class="details__cell details__cell--right details__cell--last">
            <p class="details__volume">700 ml</p>
          </div>
        </div>
      </div>

      <div class="label__base-band"></div>
    </section>
  </main>
</body>
</html>
```